Redesign 2016 Digital Marketing Website and Convert to Wordpress

Technology needed to integrate:

- redesign and convert to wordpress
- gravity forms
- malware and hacker defense / honeypot (must be very secure from hackers)
- I want gravity forms to be a flow that asks many questions with icons and progress bar.
- 1 home page design
- 1 blog design
- 1 design for internal page content
- 1 multi step gravity form
I want to focus on SMB's. We are a marketing agency thats been around since 2016.

Site is: tallpine.agency

I am looking to redesign the homepage, blog page and services page. The services page will be a template for all inner pages of the site. All content needs to be moved into the new design.

I want to get ride of the weird video.

I need you to install gravity forms pro model so we can pass utms.

I need the gravity form to be a multi step form with icons.

All "contact us" or "get a free assesments" call to actions will go to this form only.

step 1:
what is your website

step 2:
what industry are you in
- option
- Home Services
- Legal
- Ecommerce
- Lead Gen

No matter which one they select its going to produce a differnt calculator for them.

Law:
How many leads did you get last month
how much is each ase worth on average
How much revenue do you want to make

Home servicse:
How many bookings did you get last month
How much is each service worht on average
How much revenue do you wangt to make

Ecommerce:
What is your average order value
How muny purchases did you have last month
How much revenue did you drive
How much revenue do you want to drive

For lead gen:
How many leads did you get lawt month
How much revenue did they generate

Step 3:
What is your current advertising budget

step 4:
Do you have a CRM and if so what is it

Step 5:
What is your personal informagtion
name
email
phone

Let me know if this is enough to get you going

Small and medium sized law firms, ecommerce, home services and lead gen customers.

We are a digital marketing agency

• Use whats on the current site and improve upon it

• Must be very secure, developed into a wordpress website. using gravity forms. remove my photo and my staffs photo, depersonalize it so it doesnt mention me or sam crolley. Use the same color scheme. I am looking to redesign the homepage, blog page and services page. The services page will be a template for all inner pages of the site. All content needs to be moved into the new design. I want to get ride of the weird video. I need you to install gravity forms pro model so we can pass utms. I need the gravity form to be a multi step form with icons. All "contact us" or "get a free assesments" call to actions will go to this form only. step 1: what is your website step 2: what industry are you in - option - Home Services - Legal - Ecommerce - Lead Gen No matter which one they select its going to produce a differnt calculator for them. Law: How many leads did you get last month how much is each ase worth on average How much revenue do you want to make Home servicse: How many bookings did you get last month How much is each service worht on average How much revenue do you wangt to make Ecommerce: What is your average order value How muny purchases did you have last month How much revenue did you drive How much revenue do you want to drive For lead gen: How many leads did you get lawt month How much revenue did they generate How much revenue do you want to make Step 3: What is your current advertising budget step 4: Do you have a CRM and if so what is it Step 5: What is your personal informagtion name email phone Let me know if this is enough to get you going
• SHOULD NOT BE SLOPPY, I AM LOOKING FOR ATTENTION TO DETAIL.

```html
<!DOCTYPE html>
<html lang="en">
<head>
<meta charset="utf-8">
<title>Tall Pine Growth Marketing – Revenue Form Flow</title>
<link href="https://fonts.googleapis.com/css2?family=Poppins:wght@300;400;500;600;700&display=swap" rel="stylesheet">
<style>
:root{
  --stage:#6d1216;
  --brand:#7a1a1d;
  --accent:#f7941d;
  --nav:#2b2b2b;
  --ink:#2a2a2a;
  --muted:#555;
  --soft:#666;
  --line:#e6e6e6;
  --pale:#c9c9c9;
  --white:#fff;
}
*{margin:0;padding:0;box-sizing:border-box}
html,body{width:1200px;height:870px;overflow:hidden;background:var(--stage);font-family:"Poppins",sans-serif;color:var(--ink)}
.page{position:absolute;width:376px;height:405px;background:var(--white);overflow:hidden}
.page *{position:absolute}
.page span,.page b,.page em{position:static}

/* header */
.brand{left:23px;top:5px;height:19px;width:120px}
.brand .mark{left:0;top:0;width:19px;height:19px;border-radius:50%;background:var(--brand)}
.brand .name{left:24px;top:2px;font-size:7.6px;font-weight:300;letter-spacing:.8px;color:var(--soft);white-space:nowrap;line-height:1}
.brand .tag{left:25px;top:12px;font-size:2.6px;font-weight:400;letter-spacing:1.5px;color:var(--soft);white-space:nowrap}
.call{right:101px;top:11px;font-size:5.2px;font-weight:600;white-space:nowrap}
.call em{font-style:normal;color:var(--brand)}
.cta{left:281px;top:7px;width:70px;height:14px;background:var(--accent);color:var(--white);font-size:4.5px;font-weight:600;display:flex;align-items:center;justify-content:center;letter-spacing:.2px}
.nav{left:0;top:28px;width:376px;height:17px;background:var(--nav);display:flex;justify-content:center;align-items:center;gap:14px;font-size:4.3px;color:var(--white)}
.nav span{position:static}

/* form */
.title{left:0;top:62px;width:376px;text-align:center;font-size:11.6px;font-weight:700;letter-spacing:.2px}
.rule{left:174px;top:80px;width:29px;height:1.3px;background:var(--brand)}
.track{left:94px;top:103.5px;width:188px;height:1px;background:var(--pale)}
.fill{left:94px;top:103.5px;height:1px;background:var(--brand)}
.dot{top:94.5px;width:19px;height:19px;border-radius:50%;border:1px solid var(--pale);background:var(--white);color:var(--pale);font-size:7px;font-weight:600;display:flex;align-items:center;justify-content:center}
.dot.on{background:var(--brand);border-color:var(--brand);color:var(--white)}
.d1{left:84.5px}.d2{left:131.5px}.d3{left:178.5px}.d4{left:225.5px}.d5{left:272.5px}
.q-icon{left:91px;top:129px;width:14px;height:14px}
.q-step{left:109px;top:127.5px;font-size:6px;font-weight:600;color:var(--brand)}
.q-text{left:109px;top:137px;font-size:5.2px;white-space:nowrap}
.field{height:16px;border:1px solid var(--pale);font-size:3.8px;color:var(--muted);display:flex;align-items:center;padding-left:6px}
.field.wide{left:91px;top:150px;width:155px}
.next{left:249px;top:150px;width:36px;height:16px;background:var(--nav);color:var(--white);font-size:6.2px;font-weight:700;display:flex;align-items:center;justify-content:center;gap:4px}
.submit{left:250px;top:150px;width:40px;height:35px;background:var(--accent);color:var(--white);font-size:6.2px;font-weight:700;display:flex;align-items:center;justify-content:center;gap:3px}

/* footer */
.f-top{left:0;top:207px;width:376px;height:1px;background:var(--line)}
.f-brand{left:23px;top:221px}
.partner{left:130px;top:218px;width:64px;height:26px;background:#eeeeee;border-left:6px solid #e53935}
.review{left:215px;top:218px;width:27px;height:27px;border-radius:50%;background:#1f4e79;border:2px solid #d7dde5}
.follow{left:277px;top:219px;font-size:5.6px;font-weight:500;letter-spacing:.3px}
.social{left:277px;top:232px;width:90px;height:8px}
.social i{position:absolute;top:0;width:8px;height:8px;border-radius:50%;background:var(--nav)}
.f-mid{left:0;top:254px;width:376px;height:1px;background:var(--line)}
.col{top:267px}
.col h4{position:static;font-size:7.6px;font-weight:600;letter-spacing:.2px;margin-bottom:3.5px}
.col p{position:static;font-size:3.9px;color:var(--muted);line-height:5.2px;margin-bottom:5.1px;max-width:72px}
.c1{left:23px}.c2{left:99px}.c3{left:193px}.c4{left:277px}
.f-low{left:0;top:378px;width:376px;height:1px;background:var(--line)}
.copy{left:71px;top:389px;font-size:3.9px;color:var(--muted);white-space:nowrap}
.mini{left:366px;top:390px;font-size:3.6px;color:var(--muted)}
</style>
</head>
<body>

<!-- STEP 1 -->
<section class="page" style="left:23px;top:25px">
  <div class="brand"><div class="mark"></div><div class="name">TALL PINE</div><div class="tag">GROWTH MARKETING</div></div>
  <div class="call">OR CALL US NOW : <em>(555) 014-2290</em></div>
  <div class="cta">GROW YOUR REVENUE</div>
  <nav class="nav"><span>HOME</span><span>ABOUT</span><span>INDUSTRIES</span><span>SERVICES</span><span>BLOG</span><span>CONTACT US</span></nav>
  <h1 class="title">GROW YOUR REVENUE NOW</h1><div class="rule"></div>
  <div class="track"></div><div class="fill" style="width:40px"></div>
  <div class="dot d1 on">1</div><div class="dot d2">2</div><div class="dot d3">3</div><div class="dot d4">4</div><div class="dot d5">5</div>
  <svg class="q-icon" viewBox="0 0 14 14" fill="none" stroke="#7a1a1d" stroke-width=".7"><circle cx="7" cy="7" r="6"/><ellipse cx="7" cy="7" rx="2.6" ry="6"/><path d="M1 7h12M2 4h10M2 10h10"/></svg>
  <div class="q-step">Step 1</div><div class="q-text">What is your website</div>
  <div class="field wide">Enter business name</div>
  <div class="next">NEXT <span>&rsaquo;</span></div>
  <div class="f-top"></div>
  <div class="brand f-brand"><div class="mark"></div><div class="name">TALL PINE</div><div class="tag">GROWTH MARKETING</div></div>
  <div class="partner" role="img" aria-label="Partner badge"></div>
  <div class="review" role="img" aria-label="Review badge"></div>
  <div class="follow">FOLLOW US</div>
  <div class="social" role="img" aria-label="Social links"><i style="left:0"></i><i style="left:16px"></i><i style="left:32px"></i><i style="left:50px"></i><i style="left:68px"></i></div>
  <div class="f-mid"></div>
  <div class="col c1"><h4>QUICK LINKS</h4><p>About</p><p>Industries</p><p>Services</p><p>Resources</p><p>Training</p><p>Blog</p><p>Contact Us</p></div>
  <div class="col c2"><h4>SERVICES</h4><p>Programmatic Advertising</p><p>Search Engine Marketing (SEM)</p><p>Search Engine Optimization (SEO)</p><p>Content Marketing</p><p>Email Marketing</p><p>Paid Search Advertising</p><p>Paid Social Advertising</p></div>
  <div class="col c3"><h4>INDUSTRIES</h4><p>Ecommerce</p><p>Electricians</p><p>Financial Services Marketing</p><p>Home Builders</p><p>Home Services</p><p>Hvac Companies</p><p>Cosmetic Surgery Centers</p><p>Dental Marketing</p></div>
  <div class="col c4"><h4>GUIDES</h4><p>Ultimate Guide On Growing Your Medical Practice Business</p><p>Legal Marketing Strategy Guide For Law Firm Offices</p><p>Ultimate Story Ads Guide To Skyrocket Your Leads And Sales</p><p>Ultimate Guide To Search Engine Queries</p></div>
  <div class="f-low"></div>
  <div class="copy">Copyright © 2024 CompanyName &nbsp;All Rights Reserved. Privacy Policy, Terms Of Use, Press &amp; Media, Cookie Policy</div>
  <div class="mini">x10</div>
</section>

<!-- STEP 2 -->
<section class="page" style="left:414px;top:25px">
  <div class="brand"><div class="mark"></div><div class="name">TALL PINE</div><div class="tag">GROWTH MARKETING</div></div>
  <div class="call">OR CALL US NOW : <em>(555) 014-2290</em></div>
  <div class="cta">GROW YOUR REVENUE</div>
  <nav class="nav"><span>HOME</span><span>ABOUT</span><span>INDUSTRIES</span><span>SERVICES</span><span>BLOG</span><span>CONTACT US</span></nav>
  <h1 class="title">GROW YOUR REVENUE NOW</h1><div class="rule"></div>
  <div class="track"></div><div class="fill" style="width:87px"></div>
  <div class="dot d1 on">1</div><div class="dot d2 on">2</div><div class="dot d3">3</div><div class="dot d4">4</div><div class="dot d5">5</div>
  <svg class="q-icon" viewBox="0 0 14 14" fill="none" stroke="#7a1a1d" stroke-width=".7"><rect x="2" y="1" width="6" height="12"/><rect x="8" y="5" width="4" height="8"/><path d="M3.5 3h1M5.5 3h1M3.5 5.5h1M5.5 5.5h1M3.5 8h1M5.5 8h1M9.5 7.5h1M9.5 10h1M1 13h12"/></svg>
  <div class="q-step">Step 2</div><div class="q-text">What industry are you in</div>
  <div class="field wide">Enter industry</div>
  <div class="next">NEXT <span>&rsaquo;</span></div>
  <div class="f-top"></div>
  <div class="brand f-brand"><div class="mark"></div><div class="name">TALL PINE</div><div class="tag">GROWTH MARKETING</div></div>
  <div class="partner" role="img" aria-label="Partner badge"></div>
  <div class="review" role="img" aria-label="Review badge"></div>
  <div class="follow">FOLLOW US</div>
  <div class="social" role="img" aria-label="Social links"><i style="left:0"></i><i style="left:16px"></i><i style="left:32px"></i><i style="left:50px"></i><i style="left:68px"></i></div>
  <div class="f-mid"></div>
  <div class="col c1"><h4>QUICK LINKS</h4><p>About</p><p>Industries</p><p>Services</p><p>Resources</p><p>Training</p><p>Blog</p><p>Contact Us</p></div>
  <div class="col c2"><h4>SERVICES</h4><p>Programmatic Advertising</p><p>Search Engine Marketing (SEM)</p><p>Search Engine Optimization (SEO)</p><p>Content Marketing</p><p>Email Marketing</p><p>Paid Search Advertising</p><p>Paid Social Advertising</p></div>
  <div class="col c3"><h4>INDUSTRIES</h4><p>Ecommerce</p><p>Electricians</p><p>Financial Services Marketing</p><p>Home Builders</p><p>Home Services</p><p>Hvac Companies</p><p>Cosmetic Surgery Centers</p><p>Dental Marketing</p></div>
  <div class="col c4"><h4>GUIDES</h4><p>Ultimate Guide On Growing Your Medical Practice Business</p><p>Legal Marketing Strategy Guide For Law Firm Offices</p><p>Ultimate Story Ads Guide To Skyrocket Your Leads And Sales</p><p>Ultimate Guide To Search Engine Queries</p></div>
  <div class="f-low"></div>
  <div class="copy">Copyright © 2024 CompanyName &nbsp;All Rights Reserved. Privacy Policy, Terms Of Use, Press &amp; Media, Cookie Policy</div>
  <div class="mini">x10</div>
</section>

<!-- STEP 3 -->
<section class="page" style="left:806px;top:25px">
  <div class="brand"><div class="mark"></div><div class="name">TALL PINE</div><div class="tag">GROWTH MARKETING</div></div>
  <div class="call">OR CALL US NOW : <em>(555) 014-2290</em></div>
  <div class="cta">GROW YOUR REVENUE</div>
  <nav class="nav"><span>HOME</span><span>ABOUT</span><span>INDUSTRIES</span><span>SERVICES</span><span>BLOG</span><span>CONTACT US</span></nav>
  <h1 class="title">GROW YOUR REVENUE NOW</h1><div class="rule"></div>
  <div class="track"></div><div class="fill" style="width:134px"></div>
  <div class="dot d1 on">1</div><div class="dot d2 on">2</div><div class="dot d3 on">3</div><div class="dot d4">4</div><div class="dot d5">5</div>
  <svg class="q-icon" viewBox="0 0 14 14" fill="none" stroke="#7a1a1d" stroke-width=".7"><rect x="3" y="1" width="8" height="12" rx=".8"/><rect x="4.5" y="2.5" width="5" height="2.5"/><path d="M5 7h1M8 7h1M5 9h1M8 9h1M5 11h1M8 11h1"/></svg>
  <div class="q-step">Step 3</div><div class="q-text">What is your current advertising budget</div>
  <div class="field wide">Enter budget</div>
  <div class="next">NEXT <span>&rsaquo;</span></div>
  <div class="f-top"></div>
  <div class="brand f-brand"><div class="mark"></div><div class="name">TALL PINE</div><div class="tag">GROWTH MARKETING</div></div>
  <div class="partner" role="img" aria-label="Partner badge"></div>
  <div class="review" role="img" aria-label="Review badge"></div>
  <div class="follow">FOLLOW US</div>
  <div class="social" role="img" aria-label="Social links"><i style="left:0"></i><i style="left:16px"></i><i style="left:32px"></i><i style="left:50px"></i><i style="left:68px"></i></div>
  <div class="f-mid"></div>
  <div class="col c1"><h4>QUICK LINKS</h4><p>About</p><p>Industries</p><p>Services</p><p>Resources</p><p>Training</p><p>Blog</p><p>Contact Us</p></div>
  <div class="col c2"><h4>SERVICES</h4><p>Programmatic Advertising</p><p>Search Engine Marketing (SEM)</p><p>Search Engine Optimization (SEO)</p><p>Content Marketing</p><p>Email Marketing</p><p>Paid Search Advertising</p><p>Paid Social Advertising</p></div>
  <div class="col c3"><h4>INDUSTRIES</h4><p>Ecommerce</p><p>Electricians</p><p>Financial Services Marketing</p><p>Home Builders</p><p>Home Services</p><p>Hvac Companies</p><p>Cosmetic Surgery Centers</p><p>Dental Marketing</p></div>
  <div class="col c4"><h4>GUIDES</h4><p>Ultimate Guide On Growing Your Medical Practice Business</p><p>Legal Marketing Strategy Guide For Law Firm Offices</p><p>Ultimate Story Ads Guide To Skyrocket Your Leads And Sales</p><p>Ultimate Guide To Search Engine Queries</p></div>
  <div class="f-low"></div>
  <div class="copy">Copyright © 2024 CompanyName &nbsp;All Rights Reserved. Privacy Policy, Terms Of Use, Press &amp; Media, Cookie Policy</div>
  <div class="mini">x10</div>
</section>

<!-- STEP 4 -->
<section class="page" style="left:231px;top:444px">
  <div class="brand"><div class="mark"></div><div class="name">TALL PINE</div><div class="tag">GROWTH MARKETING</div></div>
  <div class="call">OR CALL US NOW : <em>(555) 014-2290</em></div>
  <div class="cta">GROW YOUR REVENUE</div>
  <nav class="nav"><span>HOME</span><span>ABOUT</span><span>INDUSTRIES</span><span>SERVICES</span><span>BLOG</span><span>CONTACT US</span></nav>
  <h1 class="title">GROW YOUR REVENUE NOW</h1><div class="rule"></div>
  <div class="track"></div><div class="fill" style="width:175px"></div>
  <div class="dot d1 on">1</div><div class="dot d2 on">2</div><div class="dot d3 on">3</div><div class="dot d4 on">4</div><div class="dot d5">5</div>
  <svg class="q-icon" viewBox="0 0 14 14" fill="none" stroke="#7a1a1d" stroke-width=".7"><circle cx="7" cy="8" r="2"/><circle cx="7" cy="2.2" r="1.3"/><circle cx="2" cy="11.5" r="1.3"/><circle cx="12" cy="11.5" r="1.3"/><path d="M7 3.5V6M3 10.8l2.4-1.6M11 10.8l-2.4-1.6"/></svg>
  <div class="q-step">Step 4</div><div class="q-text">Do you have a CRM and if so what is it</div>
  <div class="field wide">Enter CRM details</div>
  <div class="next">NEXT <span>&rsaquo;</span></div>
  <div class="f-top"></div>
  <div class="brand f-brand"><div class="mark"></div><div class="name">TALL PINE</div><div class="tag">GROWTH MARKETING</div></div>
  <div class="partner" role="img" aria-label="Partner badge"></div>
  <div class="review" role="img" aria-label="Review badge"></div>
  <div class="follow">FOLLOW US</div>
  <div class="social" role="img" aria-label="Social links"><i style="left:0"></i><i style="left:16px"></i><i style="left:32px"></i><i style="left:50px"></i><i style="left:68px"></i></div>
  <div class="f-mid"></div>
  <div class="col c1"><h4>QUICK LINKS</h4><p>About</p><p>Industries</p><p>Services</p><p>Resources</p><p>Training</p><p>Blog</p><p>Contact Us</p></div>
  <div class="col c2"><h4>SERVICES</h4><p>Programmatic Advertising</p><p>Search Engine Marketing (SEM)</p><p>Search Engine Optimization (SEO)</p><p>Content Marketing</p><p>Email Marketing</p><p>Paid Search Advertising</p><p>Paid Social Advertising</p></div>
  <div class="col c3"><h4>INDUSTRIES</h4><p>Ecommerce</p><p>Electricians</p><p>Financial Services Marketing</p><p>Home Builders</p><p>Home Services</p><p>Hvac Companies</p><p>Cosmetic Surgery Centers</p><p>Dental Marketing</p></div>
  <div class="col c4"><h4>GUIDES</h4><p>Ultimate Guide On Growing Your Medical Practice Business</p><p>Legal Marketing Strategy Guide For Law Firm Offices</p><p>Ultimate Story Ads Guide To Skyrocket Your Leads And Sales</p><p>Ultimate Guide To Search Engine Queries</p></div>
  <div class="f-low"></div>
  <div class="copy">Copyright © 2024 CompanyName &nbsp;All Rights Reserved. Privacy Policy, Terms Of Use, Press &amp; Media, Cookie Policy</div>
  <div class="mini">x10</div>
</section>

<!-- STEP 5 -->
<section class="page" style="left:633px;top:444px">
  <div class="brand"><div class="mark"></div><div class="name">TALL PINE</div><div class="tag">GROWTH MARKETING</div></div>
  <div class="call">OR CALL US NOW : <em>(555) 014-2290</em></div>
  <div class="cta">GROW YOUR REVENUE</div>
  <nav class="nav"><span>HOME</span><span>ABOUT</span><span>INDUSTRIES</span><span>SERVICES</span><span>BLOG</span><span>CONTACT US</span></nav>
  <h1 class="title">GROW YOUR REVENUE NOW</h1><div class="rule"></div>
  <div class="track"></div><div class="fill" style="width:188px"></div>
  <div class="dot d1 on">1</div><div class="dot d2 on">2</div><div class="dot d3 on">3</div><div class="dot d4 on">4</div><div class="dot d5 on">5</div>
  <svg class="q-icon" viewBox="0 0 14 14" fill="none" stroke="#7a1a1d" stroke-width=".7"><rect x="2" y="1" width="10" height="12"/><circle cx="5.5" cy="5" r="1.5"/><path d="M3.5 9c.4-1.5 3.6-1.5 4 0M8.5 4h2M8.5 6h2M4 11h6"/></svg>
  <div class="q-step">Step 5</div><div class="q-text">What is your personal information</div>
  <div class="field" style="left:91px;top:150px;width:75px">Name</div>
  <div class="field" style="left:171px;top:150px;width:75px">Phone</div>
  <div class="field" style="left:91px;top:170px;width:155px">Email Address</div>
  <div class="submit">SUBMIT <span>&rsaquo;</span></div>
  <div class="f-top"></div>
  <div class="brand f-brand"><div class="mark"></div><div class="name">TALL PINE</div><div class="tag">GROWTH MARKETING</div></div>
  <div class="partner" role="img" aria-label="Partner badge"></div>
  <div class="review" role="img" aria-label="Review badge"></div>
  <div class="follow">FOLLOW US</div>
  <div class="social" role="img" aria-label="Social links"><i style="left:0"></i><i style="left:16px"></i><i style="left:32px"></i><i style="left:50px"></i><i style="left:68px"></i></div>
  <div class="f-mid"></div>
  <div class="col c1"><h4>QUICK LINKS</h4><p>About</p><p>Industries</p><p>Services</p><p>Resources</p><p>Training</p><p>Blog</p><p>Contact Us</p></div>
  <div class="col c2"><h4>SERVICES</h4><p>Programmatic Advertising</p><p>Search Engine Marketing (SEM)</p><p>Search Engine Optimization (SEO)</p><p>Content Marketing</p><p>Email Marketing</p><p>Paid Search Advertising</p><p>Paid Social Advertising</p></div>
  <div class="col c3"><h4>INDUSTRIES</h4><p>Ecommerce</p><p>Electricians</p><p>Financial Services Marketing</p><p>Home Builders</p><p>Home Services</p><p>Hvac Companies</p><p>Cosmetic Surgery Centers</p><p>Dental Marketing</p></div>
  <div class="col c4"><h4>GUIDES</h4><p>Ultimate Guide On Growing Your Medical Practice Business</p><p>Legal Marketing Strategy Guide For Law Firm Offices</p><p>Ultimate Story Ads Guide To Skyrocket Your Leads And Sales</p><p>Ultimate Guide To Search Engine Queries</p></div>
  <div class="f-low"></div>
  <div class="copy">Copyright © 2024 CompanyName &nbsp;All Rights Reserved. Privacy Policy, Terms Of Use, Press &amp; Media, Cookie Policy</div>
  <div class="mini">x10</div>
</section>

</body>
</html>
```